The Linen Loft Co

We need a business card design for our wardrobe company.
Please visit our website www.gentlelinenlofts.com to get an idea of who we are.

```html
<!DOCTYPE html>
<html lang="en">
<head>
<meta charset="utf-8">
<title>The Linen Loft Co — Business Card</title>
<link href="https://fonts.googleapis.com/css2?family=Mulish:wght@400;700;800&display=swap" rel="stylesheet">
<style>
  :root {
    --backdrop: #161616;
    --card: #232323;
    --card-edge: #2c2c2c;
    --emboss: #3d3d3d;
    --ink: #ffffff;
    --ink-soft: #cfcfcf;
    --ink-muted: #a9a9a9;
    --strip: #f4f4f4;
  }
  * { margin: 0; padding: 0; box-sizing: border-box; }
  html, body {
    width: 1200px; height: 895px; overflow: hidden;
    background: var(--backdrop);
    font-family: "Mulish", Arial, sans-serif;
  }
  .canvas {
    position: relative; width: 1200px; height: 895px;
    display: flex; flex-direction: column; align-items: center; justify-content: center; gap: 36px;
  }
  .card {
    position: relative; width: 700px; height: 400px;
    background: var(--card);
    border: 1px solid var(--card-edge);
    box-shadow: 0 14px 30px rgba(0,0,0,.55);
    overflow: hidden;
  }
  .brand__lockup { display: inline-flex; align-items: center; gap: 16px; }
  .brand__mark { display: block; flex: none; }
  .brand__name {
    font-weight: 700; letter-spacing: .5px; text-transform: uppercase; line-height: 1.2; white-space: nowrap;
  }

  /* Front */
  .card--front .brand { position: absolute; left: 0; right: 0; top: 176px; text-align: center; }
  .card--front .brand__mark { width: 40px; height: 40px; background: var(--emboss); }
  .card--front .brand__name { color: var(--emboss); font-size: 32px; }

  /* Back */
  .card--back .brand { position: absolute; right: 48px; top: 52px; }
  .card--back .brand__mark { width: 28px; height: 28px; border: 2px solid var(--ink); }
  .card--back .brand__name { color: var(--ink); font-size: 20px; }

  .person { position: absolute; left: 48px; top: 222px; }
  .person__name { color: var(--ink); font-size: 25px; font-weight: 800; letter-spacing: 1px; text-transform: uppercase; }
  .person__role { color: var(--ink-muted); font-size: 15px; margin-top: 2px; }

  .contacts { position: absolute; left: 48px; top: 302px; list-style: none; }
  .contacts li { display: flex; align-items: center; gap: 10px; color: var(--ink-soft); font-size: 15px; letter-spacing: .4px; height: 22px; }
  .contacts svg { width: 13px; height: 13px; fill: var(--ink-soft); flex: none; }

  .address { position: absolute; right: 48px; top: 238px; color: var(--ink-muted); font-size: 15px; line-height: 1.5; letter-spacing: .4px; font-style: normal; }

  .card__strip { position: absolute; left: 0; right: 0; bottom: 0; height: 7px; background: var(--strip); }
</style>
</head>
<body>
<main class="canvas">
  <section class="card card--front" aria-label="Card front">
    <div class="brand">
      <div class="brand__lockup">
        <span class="brand__mark" aria-hidden="true"></span>
        <div class="brand__name">The Linen Loft Co</div>
      </div>
    </div>
  </section>

  <section class="card card--back" aria-label="Card back">
    <div class="brand">
      <div class="brand__lockup">
        <span class="brand__mark" aria-hidden="true"></span>
        <div class="brand__name">The Linen Loft Co</div>
      </div>
    </div>

    <div class="person">
      <div class="person__name">Daniel Hartley</div>
      <div class="person__role">Owner</div>
    </div>

    <ul class="contacts">
      <li>
        <svg viewBox="0 0 16 16" aria-hidden="true"><path d="M3.6 1.2l2.3 2.6-1.3 1.9c.8 1.9 2.3 3.5 4.3 4.5l1.8-1.3 2.7 2.2-1.3 2.9C6.6 14 1.9 9.3 1.1 3z"/></svg>
        0207 555 0184
      </li>
      <li>
        <svg viewBox="0 0 16 16" aria-hidden="true"><path d="M1 3h14v1.2L8 9 1 4.2z"/><path d="M1 5.8L8 10.6l7-4.8V13H1z"/></svg>
        info@gentlelinenlofts.com
      </li>
      <li>
        <svg viewBox="0 0 16 16" aria-hidden="true"><circle cx="8" cy="8" r="7"/><path d="M1 8h14M8 1c-3 3.5-3 10.5 0 14M8 1c3 3.5 3 10.5 0 14" stroke="#232323" stroke-width="1.1" fill="none"/></svg>
        www.gentlelinenlofts.com
      </li>
    </ul>

    <address class="address">
      Alder Court, 42 Mill Lane<br>
      London N4 7QT
    </address>

    <div class="card__strip"></div>
  </section>
</main>
</body>
</html>
```